Need a new company business card

I am looking for a new company business card. Front and back. With information on it as per below. Card should be professional. Yet clever. Simple. Modern design. Pim card, traditional size. OK with say, all black or all red backside.

Varnholt is an indie, bootstrapped magazine advancing the work of intersectional feminists busting their buts to create a just world through the power of enterprise and innovation.

Varnholt is the home and voice of entrepreneurial feminism and feminist innovators worldwide. Entrepreneurial feminists are people (of all genders) who see inequality as an innovation priority. They work to advance gender equity and/or who strive to integrate and practice feminist principles, pedagogy, values into their innovation and entrepreneurship work.
We are committed to this space being trans and queer inclusive, anti-racist, intersectional, brave, and safe. We welcome all allies. We value learning, edgy but civil discourse and integrative thinking skills.

Target Market(s)

feminists, business owners,

Industry/Entity Type

Publishing Company

Contact Information for Business Card

RD Tolliver
Founder/Publisher
4-237 Ashgrove Lane, Toronto, ON
M4T 2K8
publisher@varnholt.com
416-552-3019
www.varnholt.com

Font styles to use
Serif
Other font styles liked:
• Myriad Pro

Colors
ec1f27
000000
ffffff

Requirements
Must have
• logo
• use red, black white colours only.
Nice to have
• use the compass in pattern or creatively but not too busy please
Should not have
• Should not be too busy. Elegant.

```html
<!DOCTYPE html>
<html lang="en">
<head>
<meta charset="utf-8">
<title>Varnholt Business Card</title>
<link rel="stylesheet" href="https://fonts.googleapis.com/css2?family=Roboto:wght@400;500&display=swap">
<style>
  :root {
    --red: #ec1f27;
    --ink: #333638;
    --black: #000000;
    --white: #ffffff;
    --paper: #f4f4f3;
    --rule: #a9a9a9;
    --muted: #555a5d;
    --stage: #e6e4e1;
  }
  * { box-sizing: border-box; margin: 0; padding: 0; }
  html, body { width: 1200px; height: 886px; overflow: hidden; }
  body {
    background: var(--stage);
    font-family: "Roboto", Arial, sans-serif;
    display: flex;
    flex-direction: column;
    align-items: center;
    justify-content: center;
    gap: 56px;
  }
  .card {
    position: relative;
    width: 560px;
    height: 320px;
    box-shadow: 0 6px 18px rgba(0,0,0,.18);
    overflow: hidden;
  }

  /* Company name with a plain marker circle */
  .brand {
    position: absolute;
    display: flex;
    align-items: center;
    gap: 12px;
  }
  .brand__name {
    font-family: "Roboto", Arial, sans-serif;
    font-weight: 500;
    line-height: 1;
  }
  .brand__dot {
    width: 12px; height: 12px;
    border-radius: 50%;
    background: currentColor;
    flex: none;
  }

  /* Front (red) */
  .card--front { background: var(--red); color: var(--white); }
  .card--front .brand {
    left: 0; right: 0; top: 98px;
    justify-content: center;
  }
  .card--front .brand__name { font-size: 58px; }
  .card--front .web {
    position: absolute;
    left: 0; right: 0; bottom: 62px;
    text-align: center;
    font-size: 12px;
    letter-spacing: 7px;
  }

  /* Back (white) */
  .card--back { background: var(--paper); color: var(--ink); }
  .card--back .brand {
    right: 46px; top: 48px;
    color: var(--ink);
  }
  .card--back .brand__name { font-size: 46px; }
  .divider {
    position: absolute;
    left: 46px; right: 46px; top: 134px;
    height: 1px;
    background: var(--rule);
  }
  .address {
    position: absolute;
    right: 46px; top: 150px;
    text-align: right;
    font-size: 13px;
    font-style: normal;
    line-height: 1.35;
    color: var(--muted);
  }
  .person {
    position: absolute;
    left: 46px; top: 190px;
  }
  .person__accent {
    position: absolute;
    left: -46px; top: 2px;
    width: 20px; height: 36px;
    background: var(--red);
  }
  .person__name {
    font-weight: 500;
    font-size: 19px;
    color: var(--black);
    text-transform: uppercase;
    line-height: 1.05;
  }
  .person__role {
    font-size: 16px;
    color: var(--red);
    line-height: 1.1;
  }
  .person__rule {
    width: 150px; height: 1px;
    background: var(--rule);
    margin: 8px 0 6px;
  }
  .contact { list-style: none; font-size: 13px; color: var(--muted); }
  .contact li { display: flex; align-items: center; gap: 8px; line-height: 17px; }
  .contact svg { width: 11px; height: 11px; fill: var(--ink); flex: none; }
</style>
</head>
<body>

  <section class="card card--front" aria-label="Card front">
    <div class="brand">
      <div class="brand__name">Varnholt</div>
      <span class="brand__dot" aria-hidden="true"></span>
    </div>
    <div class="web">www.varnholt.com</div>
  </section>

  <section class="card card--back" aria-label="Card back">
    <div class="brand">
      <div class="brand__name">Varnholt</div>
      <span class="brand__dot" aria-hidden="true"></span>
    </div>
    <div class="divider"></div>
    <address class="address">
      4-237 Ashgrove Lane<br>Toronto, ON, M4T 2K8
    </address>

    <div class="person">
      <span class="person__accent"></span>
      <div class="person__name">RD Tolliver</div>
      <div class="person__role">Founder/Publisher</div>
      <div class="person__rule"></div>
      <ul class="contact">
        <li>
          <svg viewBox="0 0 24 24" aria-hidden="true"><path d="M6.6 10.8a15.5 15.5 0 0 0 6.6 6.6l2.2-2.2a1 1 0 0 1 1-.25 11.4 11.4 0 0 0 3.6.57 1 1 0 0 1 1 1V20a1 1 0 0 1-1 1A17 17 0 0 1 3 4a1 1 0 0 1 1-1h3.5a1 1 0 0 1 1 1c0 1.25.2 2.45.57 3.57a1 1 0 0 1-.25 1z"/></svg>
          416-552-3019
        </li>
        <li>
          <svg viewBox="0 0 24 24" aria-hidden="true"><path d="M2 5h20v14H2z M3.5 6.5 12 13l8.5-6.5" stroke="#f4f4f3" stroke-width="1.6"/></svg>
          publisher@varnholt.com
        </li>
        <li>
          <svg viewBox="0 0 24 24" aria-hidden="true"><circle cx="12" cy="12" r="10"/><path d="M2 12h20M12 2c3 3 3 17 0 20M12 2c-3 3-3 17 0 20" stroke="#f4f4f3" stroke-width="1.4" fill="none"/></svg>
          www.varnholt.com
        </li>
      </ul>
    </div>
  </section>

</body>
</html>
```